American cannabis tech company business card design

Pavrel.com is seeking a modern, professional, and brand-aligned business card that represents our company and its core values: Mission, Story, Values, and Impact. As an innovative cannabis company, we want a business card that is not only visually appealing but also serves as a representation of who we are and what we stand for.

Project Scope: Design a double-sided business card that integrates our brand identity and core values. Incorporate our key brand elements, ensuring a sleek and contemporary aesthetic. Visually reflect our core values (Mission, Story, Values, Impact) in a way that is engaging yet professional.

Target Market(s)

Vendors, third parties,

Contact Information for Business Card

Contact details (name, title, email, phone, website, etc.)

Font styles to use
Other font styles liked:
• Caslon, Centra

Colors

Designer to choose colors to be used in the design.

Requirements
Must have
• Pavrel.com logo and branding A creative yet clean way to integrate our core values (Mission, Story, Values, Impact) Modern typography and a well-structured layout
Nice to have
• forest green, grey, white, black
Should not have
• references to marijuana, leafs, plants, or related product

```html
<!DOCTYPE html>
<html lang="en">
<head>
<meta charset="utf-8">
<title>Pavrel.com — Business Card</title>
<link rel="stylesheet" href="https://fonts.googleapis.com/css2?family=Poppins:wght@400;600;800&display=swap">
<style>
  :root {
    --backdrop: #9c9c9c;
    --card-green: #16321a;
    --ink-white: #ffffff;
    --ink-silver: #d4d6d5;
    --divider: rgba(255, 255, 255, 0.22);
  }
  * { margin: 0; padding: 0; box-sizing: border-box; }
  html, body {
    width: 1093px; height: 1200px; overflow: hidden;
    background: var(--backdrop);
    font-family: "Poppins", sans-serif;
  }
  .canvas { position: relative; width: 1093px; height: 1200px; }
  .card {
    position: absolute; left: 265px;
    width: 580px; height: 356px;
    background: var(--card-green);
    border-radius: 24px;
    color: var(--ink-white);
  }
  .card--front { top: 226px; }
  .card--back { top: 621px; }
  .wordmark {
    position: absolute; font-weight: 800; letter-spacing: -1px;
    line-height: 1; white-space: nowrap; transform: translate(-50%, -50%);
  }
  .card--front .wordmark { left: 152px; top: 179px; font-size: 50px; color: var(--ink-white); }
  .card--back .wordmark { left: 290px; top: 178px; font-size: 60px; color: var(--ink-silver); }
  .divider {
    position: absolute; left: 289px; top: 74px;
    width: 1px; height: 209px; background: var(--divider);
  }
  .identity { position: absolute; left: 314px; top: 98px; }
  .identity__name { font-weight: 600; font-size: 21px; line-height: 1.1; letter-spacing: 0.2px; }
  .identity__title { font-weight: 400; font-size: 16.5px; line-height: 1.2; }
  .contacts { position: absolute; left: 312px; top: 175px; list-style: none; }
  .contacts__item {
    display: flex; align-items: center; gap: 5px;
    height: 26.5px; font-size: 17px; font-weight: 400;
  }
  .contacts__icon { width: 24px; height: 24px; flex: none; }
</style>
</head>
<body>
<main class="canvas">
  <section class="card card--front" aria-label="Card front">
    <div class="wordmark">PAVREL</div>
    <div class="divider"></div>
    <div class="identity">
      <p class="identity__name">DANIEL CARTER</p>
      <p class="identity__title">Managing Director</p>
    </div>
    <ul class="contacts">
      <li class="contacts__item">
        <svg class="contacts__icon" viewBox="0 0 24 24" aria-hidden="true">
          <circle cx="12" cy="12" r="12" fill="#fff"/>
          <path d="M8 6.5l2 0 1 3-1.5 1.2a7 7 0 0 0 3.8 3.8L14.5 13l3 1v2a1.5 1.5 0 0 1-1.6 1.5A10 10 0 0 1 6.5 8.1 1.5 1.5 0 0 1 8 6.5z" fill="#16321a"/>
        </svg>
        044-555 210 347
      </li>
      <li class="contacts__item">
        <svg class="contacts__icon" viewBox="0 0 24 24" aria-hidden="true">
          <circle cx="12" cy="12" r="12" fill="#fff"/>
          <rect x="6" y="8" width="12" height="8.5" fill="none" stroke="#16321a" stroke-width="1.4"/>
          <path d="M6 8l6 5 6-5M6 16.5l4.5-4M18 16.5l-4.5-4" fill="none" stroke="#16321a" stroke-width="1.2"/>
        </svg>
        hello@pavrel.com
      </li>
      <li class="contacts__item">
        <svg class="contacts__icon" viewBox="0 0 24 24" aria-hidden="true">
          <circle cx="12" cy="12" r="12" fill="#fff"/>
          <g fill="none" stroke="#16321a" stroke-width="1.1">
            <circle cx="12" cy="12" r="6"/>
            <ellipse cx="12" cy="12" rx="2.6" ry="6"/>
            <path d="M6 12h12M7 9h10M7 15h10"/>
          </g>
        </svg>
        www.pavrel.com
      </li>
    </ul>
  </section>

  <section class="card card--back" aria-label="Card back">
    <div class="wordmark">PAVREL</div>
  </section>
</main>
</body>
</html>
```